Vernac Law Business cards and stationary design project

We are looking for a stationary design for business cards (double sided), 8x10, 5x7, and legal and standard envelopes.

We would like the design to match the logo that we have already.
Color palate preferred is Teal, White, grey and any others that will look good for a professional law firm.

We would like this statement: "RELATIONSHIPS. RESPECT. RESULT" to be on the back of the business cards and maybe on the stationary if it looks good.

Please see link to website for more information: www.vernac-law.example

Target Market(s)

Potential clients that need Attorney services.

Industry/Entity Type

Law Firm

Contact Information for Business Card

We would like the front and back to be two different colors. Current business cards are teal front, grey back and are a vertical design. We are open to options with colors.

Font styles to use
Serif

Colors
33a6d7
33b8a4
b9b9b9
5c5c5c

Requirements
Must have
• Logo supplied needs to go on the card and stationary.
• Match website color palate, www.vernac-law.example
• Be professional and not too wordy.
• Criminal Law, Civil Litigation, Personal Injury, Restraining Orders need to be on the card.
Nice to have
• RELATIONSHIPS. RESPECT. RESULTS. on the back of the card.
Should not have
• Not be too busy/wordy or too flashy.

```html
<!DOCTYPE html>
<html lang="en">
<head>
<meta charset="utf-8">
<title>Vernac Law Letterhead</title>
<link rel="stylesheet" href="https://fonts.googleapis.com/css2?family=PT+Sans:wght@400;700&display=swap">
<style>
  :root {
    --backdrop: #d6d6d6;
    --paper: #f1f1f1;
    --teal: #1b7f8b;
    --ink: #5e5e5e;
    --ink-dark: #222222;
    --band: #4b4b4b;
    --band-text: #f2f2f2;
    --signature-tone: #bdbdbd;
  }
  * { margin: 0; padding: 0; box-sizing: border-box; }
  html, body {
    width: 1200px; height: 1193px; overflow: hidden;
    background: var(--backdrop);
    font-family: "PT Sans", sans-serif;
  }
  .letterhead {
    position: absolute; left: 177px; top: 112px;
    width: 768px; height: 994px;
    background: var(--paper);
    color: var(--ink);
  }
  .brand {
    position: absolute; left: 0; top: 178px; width: 344px;
    display: flex; align-items: center; justify-content: center; gap: 10px;
  }
  .brand-mark { width: 14px; height: 14px; background: var(--teal); }
  .brand-name {
    font-size: 34px; font-weight: 400; color: var(--teal); letter-spacing: 1px;
  }
  .contact {
    position: absolute; right: 56px; top: 104px;
    text-align: right; font-size: 13px; line-height: 17.5px; color: #3d3d3d;
  }
  .contact-group { margin-bottom: 7px; }
  .contact-row { display: flex; justify-content: flex-end; align-items: center; gap: 6px; }
  .contact-row svg { width: 10px; height: 11px; flex: none; }
  .contact-row .spacer { width: 10px; }
  .recipient {
    position: absolute; left: 69px; top: 294px; font-size: 13.5px; line-height: 22px;
  }
  .recipient .date { margin-bottom: 3px; }
  .recipient .line-lg { font-size: 14.5px; line-height: 19px; }
  .salutation { position: absolute; left: 69px; top: 419px; font-size: 13.5px; }
  .body {
    position: absolute; left: 69px; top: 455px; width: 636px;
    font-size: 13.6px; line-height: 18.2px;
  }
  .body p { text-indent: 7px; margin-bottom: 17.5px; }
  .signature {
    position: absolute; left: 69px; top: 786px; width: 132px; height: 50px;
    background: linear-gradient(90deg, var(--signature-tone), #d8d8d8);
    border-radius: 4px;
  }
  .signer {
    position: absolute; left: 72px; top: 840px;
    font-size: 15px; font-weight: 700; color: var(--ink-dark);
  }
  .footer-band { position: absolute; left: 0; bottom: 0; width: 768px; height: 42px; }
  .footer-text {
    position: absolute; left: 218px; bottom: 11px;
    font-size: 13.6px; color: var(--band-text); white-space: nowrap;
  }
  .footer-text .sep {
    display: inline-block; width: 1px; height: 18px; background: var(--band-text);
    vertical-align: -4px; margin: 0 6px 0 8px;
  }
</style>
</head>
<body>
<main class="letterhead">
  <div class="brand">
    <span class="brand-mark"></span>
    <span class="brand-name">Vernac Law</span>
  </div>

  <address class="contact" style="font-style:normal">
    <div class="contact-group">
      <div class="contact-row"><span>418 Harbor Crest Ave. #200</span><span class="spacer"></span></div>
      <div class="contact-row"><span>Bayview Shores, CA 90410</span>
        <svg viewBox="0 0 10 12"><path d="M5 0.8a3.6 3.6 0 0 1 3.6 3.6C8.6 7 5 11.2 5 11.2S1.4 7 1.4 4.4A3.6 3.6 0 0 1 5 0.8z" fill="none" stroke="var(--teal)" stroke-width="1.5"/><circle cx="5" cy="4.4" r="1.2" fill="var(--teal)"/></svg>
      </div>
    </div>
    <div class="contact-row"><span>(555) 014-2290</span>
      <svg viewBox="0 0 10 10"><path d="M2 1.5c1 -0.6 1.6 0.4 2 1.4s-0.8 1.2-0.6 1.8c0.4 1 1.2 1.8 2 2.2 0.6 0.2 0.8-0.8 1.6-0.6s1.8 1 1.4 2C8 9.5 5 9 3 6.8S1 2.2 2 1.5z" fill="var(--teal)"/></svg>
    </div>
    <div class="contact-row"><span>mara@vernac-law.example</span>
      <svg viewBox="0 0 10 8"><rect x="0.5" y="0.5" width="9" height="7" fill="var(--teal)"/><path d="M0.5 0.8 5 4.5 9.5 0.8" fill="none" stroke="var(--paper)" stroke-width="1"/></svg>
    </div>
    <div class="contact-row"><span>www.vernac-law.example</span>
      <svg viewBox="0 0 10 10"><circle cx="5" cy="5" r="4.6" fill="var(--teal)"/><path d="M0.6 5h8.8M5 0.4c-2 2.6-2 6.6 0 9.2M5 0.4c2 2.6 2 6.6 0 9.2" fill="none" stroke="var(--paper)" stroke-width="0.8"/></svg>
    </div>
  </address>

  <div class="recipient">
    <div class="date">December 24, 2015,</div>
    <div>To: Reid Calloway</div>
    <div class="line-lg">Northfield Group</div>
    <div class="line-lg">City,State,Zip</div>
  </div>

  <div class="salutation">Dear Mr Calloway.</div>

  <div class="body">
    <p>Lorem ipsum dolor sit amet, consectetur adipisicing elit, sed do eiusmod carte incididunt ut labore et dolore magna aliqua. Ut enim ad minim veniam, quis&nbsp; exercitation ullamco laboris nisi ut aliquip ex ea commodo consequat. review dolor in reprehenderit in voluptate .</p>
    <p>build voluptas sit aspernatur aut odit aut fugit, sed quia consequunture&nbsp; fugite ratione voluptatem equi nesciunt. Neque porro quisquam est, qui dolor ipsum sit amet, consectetur, adipisci velit, sed quia non numquam eius modilos iduim labore et dolore .</p>
    <p>Excepteur sint occaecat cupidatat non proident, sunt in culpa qui officia deser accusantium dolore mque laudantium, totam rem aperiam, eaque ipsa quae an ratione voluptatem sequi nesciunt. Nequ porro quisquam est, qui dolorem ie anim id est laborum. Sed ut perspiciatis unde omnis iste natus error sit volupte accusantium doloremque laudantium, totam rem aperiam, eaque ipsa quae ab verit atis et quasi architecto beatae vitae .</p>
    <p>Fuia voluptas sit aspernatur aut odit aut fugit, sed quia consequuntur magni&nbsp; ratione voluptatem seq ui nesciunt. Neque porro quisquam est, qui dolorem eps sit amet, consectetur, adipisci velit, sed quia non numquam eius modi tempora&nbsp; labore et dolore .</p>
  </div>

  <div class="signature" role="img" aria-label="Handwritten signature"></div>
  <div class="signer">Owen Marlow</div>

  <svg class="footer-band" viewBox="0 0 768 42" aria-hidden="true">
    <polygon points="222,0 768,0 768,42 182,42" fill="var(--band)"/>
    <polygon points="0,15 199,15 188,27 0,27" fill="var(--teal)"/>
    <polygon points="199,15 205,15 194,27 188,27" fill="var(--paper)"/>
  </svg>
  <div class="footer-text">&#9670; Criminal Law &#9670; Civil Litigation &#9670; Personal Injury<span class="sep"></span>&#9670; Relationships &#9670; Respect &#9670; Results</div>
</main>
</body>
</html>
```